Etiketten-Design für Kräuterbonbon-Metalldose
Katrin Wolber hat sehr viel Talent. Das Design ist absolut kreativ.
Zielgruppe
Unsere Firma FelvoNat verkauft verschiedene Sorten Kräuterbonbons.
Wir brauchen ein Etikett, dass auf eine Metall-Dose (Durchmesser 10 cam, Höhe ca. 3 cm) geklebt wird.
Zielgruppe: jung-alt
Aufgabenstellung
Der Name unserer Kräuterbonbons ist Moospille.
Wir möchten, dass unsere Kunden, wenn sie das Etikett sehen einen Bezug zur Schweiz herstellen können.
Wir verwenden für unsere Bonbons unterschiedliche Kräuter für verschiedene Anwendungen:
Konkret sind erstmal 4 Dosen geplant:
-Kräutermischung aus 16 Kräuter gegen Husten
-Salbei gegen Halsschmerzen
-Anis gegen Magenschmerzen
-Zitrone/Ingwer für die Nerven
Vorderseite: Produktbeschreibung
Rückseite: unsere Herstellerangaben
Größenangaben der Dose: Durchmesser 10 cm, Höhe ca. 3 cm
Im Anhang habe ich Ihnen noch weitere/ genauere Informationen zur Verfügung bereitgestellt!

```html
<!DOCTYPE html>
<html lang="de">
<head>
<meta charset="utf-8">
<title>Moospille – Etiketten für Kräuterbonbon-Dosen</title>
<link href="https://fonts.googleapis.com/css2?family=Cinzel:wght@400&family=Italianno&family=Cabin:wght@600&family=Cabin+Condensed:wght@500&display=swap" rel="stylesheet">
<style>
  :root {
    --paper: #ffffff;
    --sage: #4f8a22;
    --anise: #776e4a;
    --lemon: #f3c43c;
    --label-edge: #d9d6cc;
  }
  html, body {
    margin: 0;
    padding: 0;
    width: 1200px;
    height: 1200px;
    overflow: hidden;
    background: var(--paper);
  }
  .canvas {
    position: relative;
    width: 1200px;
    height: 1200px;
    background: var(--paper);
  }
  .brand {
    position: absolute;
    top: 110px;
    left: 0;
    width: 1200px;
    text-align: center;
    color: var(--sage);
  }
  .brand-mark {
    display: block;
    width: 56px;
    height: 56px;
    margin: 0 auto 48px;
    background: var(--sage);
  }
  .brand-name {
    margin: 0;
    font-family: "Cinzel", serif;
    font-weight: 400;
    font-size: 98px;
    line-height: 1;
    letter-spacing: 1px;
  }
  .brand-tagline {
    margin: 18px 0 0;
    font-family: "Italianno", cursive;
    font-size: 50px;
    line-height: 1;
  }
  .tins {
    position: absolute;
    left: 0;
    top: 480px;
    width: 1200px;
    height: 720px;
  }
  .label-name { font-family: "Cinzel", serif; font-size: 44px; }
  .label-tagline { font-family: "Italianno", cursive; font-size: 25px; }
  .band-title { font-family: "Cabin", sans-serif; font-weight: 600; font-size: 24px; letter-spacing: 1px; fill: var(--paper); }
  .band-sub { font-family: "Cabin Condensed", sans-serif; font-weight: 500; font-size: 18px; letter-spacing: 0.5px; fill: var(--paper); }
</style>
</head>
<body>
<div class="canvas">
  <header class="brand">
    <span class="brand-mark"></span>
    <h1 class="brand-name">MOOSPILLE</h1>
    <p class="brand-tagline">Traditional Swiss Formula</p>
  </header>

  <svg class="tins" viewBox="0 480 1200 720" xmlns="http://www.w3.org/2000/svg">
    <defs>
      <clipPath id="label-circle"><circle cx="0" cy="0" r="315"/></clipPath>
      <radialGradient id="herbs-sage" cx="50%" cy="50%" r="50%">
        <stop offset="45%" stop-color="#ffffff"/>
        <stop offset="100%" stop-color="#cfe2bd"/>
      </radialGradient>
      <radialGradient id="herbs-anise" cx="50%" cy="50%" r="50%">
        <stop offset="45%" stop-color="#ffffff"/>
        <stop offset="100%" stop-color="#dcd8c8"/>
      </radialGradient>
      <radialGradient id="herbs-lemon" cx="50%" cy="50%" r="50%">
        <stop offset="45%" stop-color="#ffffff"/>
        <stop offset="100%" stop-color="#fbe9b3"/>
      </radialGradient>
    </defs>

    <!-- Salbei -->
    <g class="tin-label tin-sage" transform="translate(198 818)">
      <g clip-path="url(#label-circle)">
        <circle r="315" fill="url(#herbs-sage)" role="img" aria-label="Linienzeichnung von Kräutern und Blüten in Grün"/>
        <rect x="-12" y="-100" width="28" height="28" fill="var(--sage)"/>
        <text class="label-name" x="2" y="-20" text-anchor="middle" fill="var(--sage)">MOOSPILLE</text>
        <text class="label-tagline" x="2" y="12" text-anchor="middle" fill="var(--sage)">Traditional Swiss Formula</text>
        <rect x="-330" y="72" width="502" height="117" fill="var(--sage)"/>
        <text class="band-title" x="-64" y="124">SALBEI</text>
        <text class="band-sub" x="-64" y="158">GEGEN HALSSCHMERZEN</text>
      </g>
      <circle r="315" fill="none" stroke="var(--label-edge)" stroke-width="3"/>
    </g>

    <!-- Anis -->
    <g class="tin-label tin-anise" transform="translate(574 832)">
      <g clip-path="url(#label-circle)">
        <circle r="315" fill="url(#herbs-anise)" role="img" aria-label="Linienzeichnung von Kräutern und Blüten in Olivbraun"/>
        <rect x="-12" y="-100" width="28" height="28" fill="var(--anise)"/>
        <text class="label-name" x="2" y="-20" text-anchor="middle" fill="var(--anise)">MOOSPILLE</text>
        <text class="label-tagline" x="2" y="12" text-anchor="middle" fill="var(--anise)">Traditional Swiss Formula</text>
        <rect x="-330" y="72" width="502" height="117" fill="var(--anise)"/>
        <text class="band-title" x="-52" y="124">ANIS</text>
        <text class="band-sub" x="-52" y="158">GEGEN MAGENSCHMERZEN</text>
      </g>
      <circle r="315" fill="none" stroke="var(--label-edge)" stroke-width="3"/>
    </g>

    <!-- Zitrone | Ingwer -->
    <g class="tin-label tin-lemon" transform="translate(958 842)">
      <g clip-path="url(#label-circle)">
        <circle r="315" fill="url(#herbs-lemon)" role="img" aria-label="Linienzeichnung von Kräutern und Blüten in Gelb"/>
        <rect x="-28" y="-100" width="28" height="28" fill="var(--lemon)"/>
        <text class="label-name" x="-14" y="-20" text-anchor="middle" fill="var(--lemon)">MOOSPILLE</text>
        <text class="label-tagline" x="-14" y="12" text-anchor="middle" fill="var(--lemon)">Traditional Swiss Formula</text>
        <rect x="-420" y="72" width="600" height="117" fill="var(--lemon)"/>
        <text class="band-title" x="-188" y="124">ZITRONE | INGWER</text>
        <text class="band-sub" x="-188" y="158">FÜR DIE NERVEN</text>
      </g>
      <circle r="315" fill="none" stroke="var(--label-edge)" stroke-width="3"/>
    </g>
  </svg>
</div>
</body>
</html>
```